PWNF Traditional Business Card Project

Please see attached....just a simple business card... on attachment- please use the exact font, style, etc as the attached "Ned Farley Broughton" card... however, replace with the "Walter Augustin Pryde" text and address below the card.

```html
<!DOCTYPE html>
<html lang="en">
<head>
<meta charset="utf-8">
<title>Walter Augustin Pryde — Business Card</title>
<link rel="stylesheet" href="https://fonts.googleapis.com/css2?family=Tinos:wght@400;700&family=Questrial&display=swap">
<style>
  :root {
    --backdrop: #5f5f5f;
    --card: #fbfbfb;
    --ink: #1c1c1c;
    --ink-soft: #3f3f3f;
    --rule: #555555;
  }
  html, body {
    margin: 0;
    padding: 0;
    width: 1200px;
    height: 1200px;
    overflow: hidden;
    background: var(--backdrop);
  }
  .card {
    position: absolute;
    left: 60px;
    top: 292px;
    width: 1080px;
    height: 616px;
    background: var(--card);
    border-radius: 26px;
    color: var(--ink);
  }
  .firm-name {
    position: absolute;
    left: 50px;
    top: 60px;
    margin: 0;
    font-family: "Tinos", "Times New Roman", serif;
    font-weight: 700;
    font-size: 44px;
    font-variant: small-caps;
    letter-spacing: 0.5px;
    line-height: 1;
  }
  .firm-suffix {
    position: absolute;
    left: 161px;
    top: 112px;
    margin: 0;
    font-family: "Tinos", "Times New Roman", serif;
    font-weight: 700;
    font-size: 20px;
    letter-spacing: 0.8px;
    color: var(--ink-soft);
  }
  .person-name {
    position: absolute;
    left: 0;
    right: 0;
    top: 302px;
    margin: 0;
    text-align: center;
    font-family: "Tinos", "Times New Roman", serif;
    font-weight: 700;
    font-size: 35px;
    letter-spacing: 1.5px;
  }
  .title-row {
    position: absolute;
    left: 43px;
    right: 43px;
    top: 356px;
    display: flex;
    align-items: center;
    gap: 20px;
  }
  .title-row .rule {
    flex: 1;
    height: 3px;
    background: var(--rule);
  }
  .title-row .job-title {
    font-family: "Questrial", "Helvetica", sans-serif;
    font-size: 26px;
    letter-spacing: 0.6px;
    color: var(--ink-soft);
  }
  .contact {
    position: absolute;
    top: 436px;
    font-family: "Questrial", "Helvetica", sans-serif;
    font-size: 24px;
    letter-spacing: 1.4px;
    color: var(--ink-soft);
    line-height: 37px;
  }
  .contact-left { left: 44px; }
  .contact-right { right: 43px; text-align: right; }
  .contact .line {
    display: flex;
    align-items: center;
    gap: 10px;
    height: 38px;
  }
  .contact-right .line { justify-content: flex-end; }
  .smallcaps { font-variant: small-caps; font-size: 25px; }
  .icon { width: 25px; height: 25px; flex: none; }
</style>
</head>
<body>
  <main class="card">
    <h1 class="firm-name">Pacific Westland</h1>
    <p class="firm-suffix">NORFIELD GROUP, PLC</p>

    <h2 class="person-name">WALTER AUGUSTIN PRYDE</h2>
    <div class="title-row">
      <span class="rule"></span>
      <span class="job-title">ATTORNEY AT LAW</span>
      <span class="rule"></span>
    </div>

    <div class="contact contact-left">
      <div class="line">2740 ALDER STREET, SUITE B</div>
      <div class="line">OAK HOLLOW, CA 90312</div>
      <div class="line smallcaps">
        <svg class="icon" viewBox="0 0 24 24" aria-hidden="true">
          <circle cx="12" cy="12" r="12" fill="#1c1c1c"/>
          <circle cx="12" cy="12" r="6.5" fill="none" stroke="#fff" stroke-width="1.6"/>
          <ellipse cx="12" cy="12" rx="2.8" ry="6.5" fill="none" stroke="#fff" stroke-width="1.4"/>
          <line x1="5.5" y1="12" x2="18.5" y2="12" stroke="#fff" stroke-width="1.4"/>
        </svg>
        www.lawspwnf.com
      </div>
    </div>

    <div class="contact contact-right">
      <div class="line">(555) 214-0187
        <svg class="icon" viewBox="0 0 24 24" aria-hidden="true">
          <circle cx="12" cy="12" r="12" fill="#1c1c1c"/>
          <path d="M8.2 6.5l2 2.6-1.1 1.4c.8 1.7 2 2.9 3.7 3.7l1.4-1.1 2.6 2-1.3 1.9c-4.4-.4-8.8-4.8-9.2-9.2z" fill="#fff"/>
        </svg>
      </div>
      <div class="line">(555) 214-0192
        <svg class="icon" viewBox="0 0 24 24" aria-hidden="true">
          <circle cx="12" cy="12" r="12" fill="#1c1c1c"/>
          <rect x="8.5" y="6" width="7" height="3.5" fill="#fff"/>
          <rect x="6" y="10" width="12" height="5.5" rx="1" fill="#fff"/>
          <rect x="8.5" y="14" width="7" height="4" fill="#fff" stroke="#1c1c1c" stroke-width="0.8"/>
        </svg>
      </div>
      <div class="line smallcaps">wpryde@lawspwnf.com
        <svg class="icon" viewBox="0 0 24 24" aria-hidden="true">
          <circle cx="12" cy="12" r="12" fill="#1c1c1c"/>
          <rect x="6" y="7.5" width="12" height="9" rx="1" fill="#fff"/>
          <path d="M6.5 8.3l5.5 4.4 5.5-4.4" fill="none" stroke="#1c1c1c" stroke-width="1.2"/>
        </svg>
      </div>
    </div>
  </main>
</body>
</html>
```